Growing Plumbing company requires signage for vans/trucks plus letterhead and business cards

Pelkey's Plumbing and Heating (see www.pelkeysnf.ca) is a well established plumbing and heating company that has been servicing the new construction, renovation and plumbing maintenance needs of residential and commercial clients for over 40 years. It operates in St. John's, Newfoundland and Labrador, Canada..

The company is now expanding into a new line of business (electrical contracting) and requires a slight modification to its existing logo. The change is from "Pelkey's Plumbing and Heating" to "Pelkey's Plumbing and Electrical". An existing raw data file is provided to allow for this slight change. NO OTHER CHANGE TO THE LOGO IS REQUIRED.

As a result of this logo change, the company would like to create a new corporate identity package that includes the following:

- Signage for company vans (sample provided with new suggestions requested)

- Signage for company trucks (simple sign on driver and passenger doors and on tailgate) (no sample exists).

- Corporate letter head (sample provided with new suggestions requested)

- Business cards (sample provided with new suggestions requested)
Updates

Hello all, 

To clarify: work on the corporate logo only requires the word change from "Heating" to "Electric". No other changes are requested on the logo. ie no changes to "D", etc. 

As a result of this slight logo change, we are also requesting suggestions that could be made to existing corporate signage, letterhead, etc. 

Thanks, 

The Pelkey's Team. 

The exact font files to be used have been uploaded.

To clarify on corporate name: 

It is to be "Pelkey's Plumbing and Electrical"   (Not Heating or Electric)

The Pelkey's Team

Industry/Entity Type

Residential

Logo Text

Pelkey's Plumbing and Electrical

Requirements
Must have
• For van and truck signage, we want something that is "clean". Phone number, website, and logo must be included.

For logo, except for change from "heating" to "electrical" no other changes are requested.

For the logo change, we will require logo to be provided for all reproduction requirements including vertical (stacked) and horizontal treatments; black & white / colour / reverse; file formats including vector (designer use) and jpeg/pdf/gif, etc. (user use); variety of sizes in all files (i.e. small, medium and large).
Nice to have
• An idea would be to have the business cards, signage and letterhead use the grey bars in the "D" of the logo as a background or to the side.

```html
<!DOCTYPE html>
<html lang="en">
<head>
<meta charset="utf-8">
<title>Pelkey's Plumbing and Electrical — Business Cards</title>
<link rel="stylesheet" href="https://fonts.googleapis.com/css2?family=Roboto:wght@300;400;700&display=swap">
<style>
  :root {
    --navy: #1d3f6e;
    --steel: #7d8084;
    --text-grey: #6b6e72;
    --card: #e9eaeb;
    --backdrop: #d4d5d7;
  }
  * { box-sizing: border-box; margin: 0; padding: 0; }
  html, body {
    width: 1200px;
    height: 900px;
    overflow: hidden;
    background: var(--backdrop);
    font-family: "Roboto", Arial, sans-serif;
  }
  .canvas {
    position: relative;
    width: 1200px;
    height: 900px;
  }
  .card {
    position: absolute;
    left: 280px;
    width: 640px;
    height: 366px;
    background: var(--card);
    box-shadow: 0 6px 18px rgba(0,0,0,0.18);
    overflow: hidden;
  }
  .card--back { top: 60px; }
  .card--front { top: 474px; }

  .edge-band {
    position: absolute;
    top: 0;
    bottom: 0;
    width: 18px;
    background: var(--navy);
  }
  .edge-accent {
    position: absolute;
    bottom: 0;
    width: 6px;
    height: 70px;
    background: var(--steel);
  }
  .card--back .edge-band { right: 0; }
  .card--back .edge-accent { right: 26px; }
  .card--front .edge-band { left: 0; }
  .card--front .edge-accent { left: 26px; }

  .wordmark {
    display: flex;
    align-items: center;
    gap: 12px;
    color: var(--navy);
    font-weight: 700;
    text-transform: uppercase;
    line-height: 1.05;
  }
  .wordmark__mark {
    flex: none;
    background: var(--navy);
  }
  .card--back .wordmark {
    position: absolute;
    left: 0;
    right: 0;
    top: 140px;
    justify-content: center;
    font-size: 30px;
  }
  .card--back .wordmark__mark { width: 46px; height: 46px; }
  .wordmark__sub {
    display: block;
    font-size: 0.5em;
    letter-spacing: 0.04em;
  }

  .card--front .wordmark {
    position: absolute;
    left: 62px;
    top: 48px;
    font-size: 28px;
  }
  .card--front .wordmark__mark { width: 42px; height: 42px; }

  .holder {
    position: absolute;
    left: 62px;
    top: 176px;
    color: var(--text-grey);
  }
  .holder__name {
    font-size: 25px;
    font-weight: 300;
    letter-spacing: 0.02em;
    text-transform: uppercase;
  }
  .holder__role {
    font-size: 17px;
    font-weight: 300;
    margin-top: 4px;
  }
  .website {
    position: absolute;
    left: 62px;
    bottom: 38px;
    color: var(--navy);
    font-size: 17px;
    font-weight: 700;
  }

  .contact {
    position: absolute;
    left: 400px;
    top: 56px;
    color: var(--text-grey);
    font-size: 14px;
    font-weight: 300;
    line-height: 1.45;
  }
  .contact__row { display: flex; gap: 14px; }
  .contact__label { width: 10px; font-weight: 400; }
  .contact__address { margin-top: 24px; padding-left: 24px; }
</style>
</head>
<body>
<main class="canvas">

  <section class="card card--back" aria-label="Business card back">
    <div class="edge-band"></div>
    <div class="edge-accent"></div>
    <div class="wordmark">
      <span class="wordmark__mark"></span>
      <span>Pelkey's<span class="wordmark__sub">Plumbing and Electrical</span></span>
    </div>
  </section>

  <section class="card card--front" aria-label="Business card front">
    <div class="edge-band"></div>
    <div class="edge-accent"></div>

    <div class="wordmark">
      <span class="wordmark__mark"></span>
      <span>Pelkey's<span class="wordmark__sub">Plumbing and Electrical</span></span>
    </div>

    <div class="holder">
      <p class="holder__name">Marla Quinlan</p>
      <p class="holder__role">Director</p>
    </div>

    <p class="website">www.pelkeysnf.ca</p>

    <div class="contact">
      <div class="contact__row"><span class="contact__label">T</span><span>709.555.0142</span></div>
      <div class="contact__row"><span class="contact__label">E</span><span>info@pelkeysnf.ca</span></div>
      <address class="contact__address" style="font-style: normal;">
        48 Harbourview Rd<br>
        Paradise NL<br>
        A1L 0X2
      </address>
    </div>
  </section>

</main>
</body>
</html>
```